Cover and back of brochure

Our company sells all kind of filters. Now we are planning to create an image brochure for our company. This brochure should represent our high quality standard, our competence and the trust of the clients in our company.

In the attachment I added covers of other catalogs which we like. Furthermore I added nice pictures in the attachment which were downloaded from brivalone. In the first place we downloaded these pictures in a small size, so that several examples can be created. After we decide which picture looks best on the cover, we will buy it in a higher resolution.

More information you find in the added pdf document.

Industry/Entity Type

It Company

Colors

Designer to choose colors to be used in the design.

```html
<!DOCTYPE html>
<html lang="de">
<head>
<meta charset="utf-8">
<title>Filter Brandt – Broschüre Umschlag</title>
<link rel="stylesheet" href="https://fonts.googleapis.com/css2?family=Oswald:wght@400;500;600&family=Roboto:wght@400;700&display=swap">
<style>
  :root {
    --bg: #8d8d8d;
    --paper: #e2eedb;
    --paper-light: #edf5e8;
    --brand-green: #1f7a3a;
    --cover-green-dark: #4a8a2a;
    --cover-green-mid: #7aad45;
    --cover-green-light: #9cc463;
    --accent-line: #8fc04a;
  }
  * { box-sizing: border-box; margin: 0; padding: 0; }
  html, body { width: 1200px; height: 800px; overflow: hidden; }
  body {
    background: var(--bg);
    font-family: "Roboto", Arial, sans-serif;
    position: relative;
  }
  .spread {
    position: absolute;
    left: 105px;
    top: 110px;
    width: 990px;
    height: 560px;
    display: flex;
  }
  .page {
    position: relative;
    width: 495px;
    height: 560px;
    overflow: hidden;
  }
  .page--back {
    background: linear-gradient(160deg, var(--paper-light), var(--paper));
  }
  .brand { color: var(--brand-green); }
  .brand__name {
    font-family: "Oswald", sans-serif;
    font-weight: 600;
    font-size: 24px;
    line-height: 1;
    letter-spacing: 0.5px;
    display: inline-flex;
    align-items: center;
    gap: 6px;
    white-space: nowrap;
  }
  .brand__dot {
    width: 12px;
    height: 12px;
    border-radius: 50%;
    background: var(--brand-green);
    display: inline-block;
  }
  .brand__owner { font-size: 10px; margin-top: 2px; }
  .brand__unit {
    font-weight: 700;
    font-size: 10px;
    letter-spacing: 0.4px;
    margin-top: 2px;
  }
  .brand__claim {
    font-family: "Oswald", sans-serif;
    font-weight: 500;
    font-size: 7px;
    letter-spacing: 0.3px;
    margin-top: 2px;
  }
  .page--back .brand {
    position: absolute;
    left: 0; right: 0;
    top: 238px;
    text-align: center;
  }
  .contact {
    position: absolute;
    left: 0; right: 0;
    bottom: 32px;
    text-align: center;
    color: var(--brand-green);
    font-size: 8.5px;
    font-weight: 700;
    font-style: normal;
    line-height: 1.55;
  }
  .page--front { background: var(--paper); }
  .cover-photo {
    position: absolute;
    inset: 0;
    background: linear-gradient(170deg, var(--cover-green-dark) 0%, var(--cover-green-mid) 50%, var(--cover-green-light) 100%);
  }
  .cover-title {
    position: absolute;
    top: 48px;
    left: 0; right: 0;
    text-align: center;
    font-family: "Oswald", sans-serif;
    font-weight: 400;
    font-size: 21px;
    letter-spacing: 1px;
    color: #ffffff;
  }
  .cover-corner { position: absolute; inset: 0; }
  .page--front .brand {
    position: absolute;
    right: 14px;
    bottom: 18px;
    text-align: right;
  }
  .page--front .brand__name { font-size: 20px; }
</style>
</head>
<body>
  <main class="spread">
    <section class="page page--back">
      <div class="brand">
        <div class="brand__name"><span class="brand__dot"></span>FILTER BRANDT</div>
        <div class="brand__owner">Jonas Kettler</div>
        <div class="brand__unit">WERKSVERTRETUNGEN</div>
        <div class="brand__claim">KOMPETENT. HILFSBEREIT. FREUNDLICH.</div>
      </div>
      <address class="contact">
        FILTER - BRANDT e.K. Inhaber Jonas Kettler Lindenweg 14 10115 Berlin<br>
        Tel: 030 / 555 0142 | Fax: 030 / 555 0143<br>
        E-Mail: info@filter-brandt.de | Web: www.filter-brandt.de
      </address>
    </section>

    <section class="page page--front">
      <div class="cover-photo" role="img" aria-label="Titelfoto: einzelner Laubbaum auf grünem Feld unter hellem Himmel"></div>
      <h1 class="cover-title">FILTERKOMPETENZ HAT EINEN NAMEN</h1>
      <svg class="cover-corner" width="495" height="560" viewBox="0 0 495 560" aria-hidden="true">
        <path d="M495 260 C 480 400, 380 500, 200 560 L495 560 Z" fill="var(--paper)"/>
        <path d="M495 260 C 480 400, 380 500, 200 560" fill="none" stroke="var(--accent-line)" stroke-width="5"/>
      </svg>
      <div class="brand">
        <div class="brand__name"><span class="brand__dot"></span>FILTER BRANDT</div>
        <div class="brand__owner">Jonas Kettler</div>
        <div class="brand__unit">WERKSVERTRETUNGEN</div>
      </div>
    </section>
  </main>
</body>
</html>
```